Local fast-growing company in the service sector

We are looking for a modern business card design, which should also appear on our letterheads

Target Market(s)

Private and industrial sectors

Contact Information for Business Card

Vorname Name
Kellberger Str. 18
71846 Lindenau
Tel.: 07146-839214-0
Name@agentur-kvtl.de

Colors
9d9d9d
919191
aaaaaa

Requirements
Must have
• The logo (file) in silver

```html
<!DOCTYPE html>
<html lang="de">
<head>
<meta charset="utf-8">
<title>KVTL – Visitenkarte</title>
<link href="https://fonts.googleapis.com/css2?family=Work+Sans:wght@400;500;700&display=swap" rel="stylesheet">
<style>
  :root {
    --page-bg: #e4e4e4;
    --card-silver: #a7a8aa;
    --ink: #111111;
    --white: #ffffff;
    --icon: #333333;
    --shadow: rgba(0, 0, 0, 0.18);
  }
  * { margin: 0; padding: 0; box-sizing: border-box; }
  html, body {
    width: 1200px;
    height: 801px;
    overflow: hidden;
    background: var(--page-bg);
    font-family: "Work Sans", Arial, sans-serif;
  }
  .canvas {
    position: relative;
    width: 1200px;
    height: 801px;
    display: flex;
    align-items: center;
    justify-content: center;
  }
  .business-card {
    position: relative;
    width: 900px;
    height: 540px;
    background: var(--card-silver);
    box-shadow: 0 12px 30px var(--shadow);
  }
  .brand {
    position: absolute;
    left: 90px;
    top: 45px;
    display: flex;
    align-items: center;
    gap: 14px;
  }
  .brand-mark {
    width: 64px;
    height: 64px;
    background: var(--white);
  }
  .brand-name {
    font-weight: 700;
    font-size: 62px;
    line-height: 1;
    letter-spacing: 1px;
    color: var(--white);
  }
  .contact-block {
    position: absolute;
    left: 535px;
    top: 150px;
    color: var(--ink);
  }
  .person-name {
    font-weight: 500;
    font-size: 29px;
    letter-spacing: 0.3px;
    line-height: 1.1;
  }
  .person-role {
    font-size: 15px;
    color: var(--white);
    letter-spacing: 1px;
    margin: 2px 0 0 12px;
  }
  .address {
    font-style: normal;
    font-size: 20px;
    line-height: 1.35;
    margin: 16px 0 0 24px;
  }
  .contact-list {
    list-style: none;
    margin: 16px 0 0 40px;
    font-size: 20px;
    line-height: 1.45;
  }
  .contact-list li {
    display: flex;
    align-items: center;
    gap: 14px;
  }
  .contact-icon {
    width: 13px;
    height: 13px;
    flex: none;
  }
</style>
</head>
<body>
<main class="canvas">
  <section class="business-card" aria-label="Visitenkarte">
    <div class="brand">
      <span class="brand-mark" aria-hidden="true"></span>
      <span class="brand-name">KVTL</span>
    </div>

    <div class="contact-block">
      <h1 class="person-name">JONAS WEBER</h1>
      <p class="person-role">DIRECTOR</p>
      <address class="address">
        Kellberger Str. 18<br>
        71846 Lindenau
      </address>
      <ul class="contact-list">
        <li>
          <svg class="contact-icon" viewBox="0 0 24 24" aria-hidden="true">
            <path fill="var(--icon)" d="M6.6 10.8a15.1 15.1 0 0 0 6.6 6.6l2.2-2.2a1 1 0 0 1 1-.25 11.4 11.4 0 0 0 3.6.57 1 1 0 0 1 1 1V20a1 1 0 0 1-1 1A17 17 0 0 1 3 4a1 1 0 0 1 1-1h3.5a1 1 0 0 1 1 1c0 1.25.2 2.45.57 3.6a1 1 0 0 1-.25 1z"/>
          </svg>
          <span>07146-839214-0</span>
        </li>
        <li>
          <svg class="contact-icon" viewBox="0 0 24 24" aria-hidden="true">
            <rect x="3" y="5" width="18" height="14" fill="none" stroke="var(--icon)" stroke-width="2"/>
            <path d="M3 6l9 7 9-7" fill="none" stroke="var(--icon)" stroke-width="2"/>
          </svg>
          <span>Name@agentur-kvtl.de</span>
        </li>
      </ul>
    </div>
  </section>
</main>
</body>
</html>
```